Harbor Crestline (Business Card Design)

Need business cards designed. Something modern, chic, and sleek. Mabye the back of the card should be the navy blue that is in the logo and then just the logo on the back.

Target Market(s)

Those in the hotel, office, and renovation industry

Contact Information for Business Card

1. Logo 2. Dorian Fenwick 3. CEO/Founder 4. Phone: (833) HarbCre / (833) 427-2731 5. Email: dorian@theharborcrestline.com 6. Website: www.theharborcrestline.com

Font styles to use
Other font styles liked:
• Look at the logo font and base the font for everything else off of that.

Colors
0054AA
0677BA
7BADD7
CADEEF
E8F1F8

Requirements
Must have
• Colors that are associated in the logo
Nice to have
• Sleek modern clean and chic design.

```html
<!DOCTYPE html>
<html lang="en">
<head>
<meta charset="utf-8">
<title>Harbor Crestline – Business Card</title>
<link rel="stylesheet" href="https://fonts.googleapis.com/css2?family=Open+Sans:wght@400;600;700&display=swap">
<style>
  :root {
    --navy: #0c1a4a;
    --navy-deep: #081236;
    --navy-light: #1d2f72;
    --gold: #c9a03c;
    --paper: #f6f6f6;
    --ink: #1b1b1f;
    --backdrop: #e6e7eb;
  }
  * { box-sizing: border-box; margin: 0; padding: 0; }
  html, body { width: 1200px; height: 780px; overflow: hidden; }
  body {
    background: var(--backdrop);
    font-family: "Open Sans", Arial, sans-serif;
    display: flex;
    align-items: center;
    justify-content: center;
    gap: 40px;
  }
  .card {
    position: relative;
    width: 560px;
    height: 320px;
    border-radius: 6px;
    overflow: hidden;
    box-shadow: 0 8px 24px rgba(8, 18, 54, 0.18);
  }

  /* Front */
  .card-front { background: var(--paper); color: var(--ink); }
  .front-swoosh { position: absolute; inset: 0; width: 100%; height: 100%; }
  .wordmark {
    position: absolute;
    display: flex;
    align-items: center;
    gap: 12px;
    font-weight: 700;
    letter-spacing: 0.08em;
    text-transform: uppercase;
    white-space: nowrap;
  }
  .card-front .wordmark { top: 50px; left: 214px; font-size: 22px; color: var(--navy); }
  .wordmark-square { width: 30px; height: 30px; background: var(--navy); flex: none; }
  .identity {
    position: absolute;
    top: 126px;
    right: 306px;
    text-align: right;
    white-space: nowrap;
  }
  .person-name { font-size: 24px; font-weight: 700; line-height: 1.15; }
  .person-first { color: var(--gold); }
  .person-last { color: var(--navy); }
  .person-title { font-size: 13px; margin-top: 2px; }
  .divider {
    position: absolute;
    top: 128px;
    left: 266px;
    width: 2px;
    height: 62px;
    background: var(--ink);
  }
  .contact-list {
    position: absolute;
    top: 130px;
    left: 282px;
    list-style: none;
    font-size: 12.5px;
    line-height: 20px;
  }
  .contact-list li { display: flex; align-items: center; gap: 7px; white-space: nowrap; }
  .contact-icon { width: 12px; height: 12px; flex: none; }
  .address {
    position: absolute;
    left: 28px;
    bottom: 14px;
    color: #fff;
    font-size: 13px;
    letter-spacing: 0.01em;
    white-space: nowrap;
  }

  /* Back */
  .card-back {
    background: linear-gradient(120deg, var(--navy-deep) 0%, var(--navy) 55%, var(--navy-light) 100%);
  }
  .back-pattern {
    position: absolute;
    inset: 0;
    background: linear-gradient(120deg, rgba(255,255,255,0) 40%, rgba(255,255,255,0.12) 100%);
  }
  .card-back .wordmark { right: 40px; bottom: 44px; font-size: 15px; color: #fff; gap: 9px; }
  .card-back .wordmark-square { width: 18px; height: 18px; background: #fff; }
</style>
</head>
<body>

  <section class="card card-front" aria-label="Business card front">
    <svg class="front-swoosh" viewBox="0 0 560 320" preserveAspectRatio="none" aria-hidden="true">
      <path d="M0 160 C140 245 360 282 560 290 L560 320 L0 320 Z" fill="var(--navy)"/>
      <path d="M10 150 C145 232 365 270 552 276" fill="none" stroke="var(--gold)" stroke-width="4" stroke-linecap="round"/>
    </svg>

    <div class="wordmark"><span class="wordmark-square"></span>Harbor Crestline</div>

    <div class="identity">
      <p class="person-name"><span class="person-first">Dorian</span> <span class="person-last">Fenwick</span></p>
      <p class="person-title">CEO/Founder</p>
    </div>

    <span class="divider"></span>

    <ul class="contact-list">
      <li>
        <svg class="contact-icon" viewBox="0 0 12 12" aria-hidden="true"><path d="M2.5 1 L4.5 1 L5.3 3.5 L4 4.5 C4.6 6 6 7.4 7.5 8 L8.5 6.7 L11 7.5 L11 9.5 C11 10.3 10.3 11 9.5 11 C5 11 1 7 1 2.5 C1 1.7 1.7 1 2.5 1 Z" fill="var(--gold)"/></svg>
        (833) HarbCre / (833) 427-2731
      </li>
      <li>
        <svg class="contact-icon" viewBox="0 0 12 12" aria-hidden="true"><circle cx="6" cy="6" r="5" fill="none" stroke="var(--gold)" stroke-width="1.4"/><path d="M1 6 H11 M6 1 C3.5 4 3.5 8 6 11 M6 1 C8.5 4 8.5 8 6 11" fill="none" stroke="var(--gold)" stroke-width="1"/></svg>
        www.theharborcrestline.com
      </li>
      <li>
        <svg class="contact-icon" viewBox="0 0 12 12" aria-hidden="true"><rect x="1" y="2.5" width="10" height="7" rx="1" fill="var(--gold)"/><path d="M1.5 3 L6 6.5 L10.5 3" fill="none" stroke="#fff" stroke-width="1"/></svg>
        dorian@theharborcrestline.com
      </li>
    </ul>

    <p class="address">4120 Larkmoor Ave Suite 210, Easton, MD 21601</p>
  </section>

  <section class="card card-back" aria-label="Business card back">
    <div class="back-pattern" role="img" aria-label="Repeating pattern of the company mark across the navy back"></div>
    <div class="wordmark"><span class="wordmark-square"></span>Harbor Crestline</div>
  </section>

</body>
</html>
```